Tall Fern Roofing Business Card

Need a business card with the logo that was designed here

Contact Information for Business Card

Name, Title, Phone, Email, Website, Company name

```html
<!DOCTYPE html>
<html lang="en">
<head>
<meta charset="utf-8">
<title>Tall Fern Roofing Business Card</title>
<link href="https://fonts.googleapis.com/css2?family=Open+Sans:wght@400;600;700&display=swap" rel="stylesheet">
<style>
  :root {
    --brand-blue: #1c74bd;
    --brand-grey: #909296;
    --ink: #2b2b2b;
    --paper: #ffffff;
    --backdrop: #e9e9ea;
  }
  * { box-sizing: border-box; margin: 0; padding: 0; }
  html, body { width: 1200px; height: 801px; overflow: hidden; }
  body {
    background: var(--backdrop);
    font-family: "Open Sans", Arial, sans-serif;
    position: relative;
  }
  .card {
    position: absolute;
    width: 520px;
    height: 297px;
    background: var(--paper);
    border-radius: 16px;
    overflow: hidden;
    box-shadow: 0 0 0 2px var(--brand-blue), 0 10px 24px rgba(0,0,0,.12);
  }
  .card--back { left: 340px; top: 70px; }
  .card--front { left: 340px; top: 430px; }

  .wordmark {
    display: flex;
    align-items: center;
    gap: 10px;
    color: var(--brand-blue);
    font-weight: 700;
    white-space: nowrap;
  }
  .wordmark__mark {
    width: 14px; height: 14px;
    background: var(--brand-blue);
    flex: none;
  }

  .card--back .wordmark {
    position: absolute;
    left: 28px; top: 128px;
    font-size: 22px;
  }
  .divider {
    position: absolute;
    left: 262px; top: 36px;
    width: 2px; height: 196px;
    background: var(--brand-blue);
  }
  .contact {
    position: absolute;
    left: 286px; top: 34px;
    color: var(--ink);
    font-size: 13.5px;
    line-height: 1.35;
  }
  .contact__name {
    color: var(--brand-blue);
    font-weight: 700;
    font-size: 21px;
    letter-spacing: .3px;
    line-height: 1.1;
  }
  .contact__title { font-size: 13px; margin-bottom: 16px; }
  .contact__address { margin-bottom: 16px; }
  .contact__row { display: flex; align-items: center; gap: 7px; }
  .contact__row svg { width: 12px; height: 12px; flex: none; }

  .edge-band {
    position: absolute;
    left: 0; bottom: 0;
    width: 100%; height: 20px;
  }

  .card--front .wordmark {
    position: absolute;
    left: 50%; top: 50%;
    transform: translate(-50%, -50%);
    font-size: 38px;
  }
  .card--front .wordmark__mark { width: 22px; height: 22px; }
</style>
</head>
<body>

  <section class="card card--back" aria-label="Business card, contact side">
    <div class="wordmark"><span class="wordmark__mark"></span>Tall Fern Roofing</div>
    <div class="divider"></div>
    <div class="contact">
      <div class="contact__name">OWEN HARTLEY</div>
      <div class="contact__title">Managing Director</div>
      <div class="contact__address">Your address, City<br>State, Zip 1234</div>
      <div class="contact__row">
        <svg viewBox="0 0 12 12"><path fill="var(--brand-blue)" d="M2.2 1l2 2-1 1.3c.7 1.5 1.9 2.7 3.4 3.4L7.9 6.7l2 2-1.2 1.8C4.8 10.3 1.6 7.1 1.5 3.2z"/></svg>
        123 456 789
      </div>
      <div class="contact__row">
        <svg viewBox="0 0 12 12"><rect x="1" y="2.5" width="10" height="7" fill="var(--brand-blue)"/><path d="M1 2.5l5 4 5-4" stroke="#fff" fill="none"/></svg>
        info@yourmail.com
      </div>
      <div class="contact__row">
        <svg viewBox="0 0 12 12"><circle cx="6" cy="6" r="5" fill="var(--brand-blue)"/><path d="M1 6h10M6 1c-2.5 3-2.5 7 0 10M6 1c2.5 3 2.5 7 0 10" stroke="#fff" stroke-width=".8" fill="none"/></svg>
        www.yourwebsite.com
      </div>
    </div>
    <svg class="edge-band" viewBox="0 0 520 20" preserveAspectRatio="none">
      <polygon points="0,0 286,0 280,20 0,20" fill="var(--brand-blue)"/>
      <polygon points="292,0 520,0 520,20 286,20" fill="var(--brand-grey)"/>
    </svg>
  </section>

  <section class="card card--front" aria-label="Business card, logo side">
    <div class="wordmark"><span class="wordmark__mark"></span>Tall Fern Roofing</div>
  </section>

</body>
</html>
```